Business card design for new eCommerce site focusing on integrity and strong businsess tactics

We need a business card that will stand out and be memorable. Something with color that matches our company logo colors. Think high end version of Pactivo. There are 2 logos provided. The parent company is called Amber Ledge Partners and we are presenting a new and very exciting eCommerce site called BrightHarborTrade.example.

Target Market(s)

Our target markets are in the Activities, Food and Beverage, Health and Beauty

Industry/Entity Type

Marketing

Contact Information for Business Card

We have 4 members that need cards...I will provide all info to the winner of the design contest
Business Address is
4870 West 63rd Avenue, Suite C207
Phoenix AZ 85731

Font styles to use
Serif
Sans Serif

Colors

Designer to choose colors to be used in the design.

Requirements
Must have
• The card must be memorable...should be unique in design but must exude integrity and be playful .
• I have provided several colors or our parent company...please feel free to use which ever
Nice to have
• I will leave this up to you. Feel free to use other images of your choosing that wraps around our client.....Activities, Dining, Health, Beauty
Should not have
• just dont be boring

```html
<!DOCTYPE html>
<html lang="en">
<head>
<meta charset="utf-8">
<title>Business Card – Front and Back</title>
<link href="https://fonts.googleapis.com/css2?family=Montserrat:wght@400;500;600;700&display=swap" rel="stylesheet">
<style>
  :root {
    --stage: #2b2b2b;
    --card: #1f1f20;
    --card-edge: #3aa8a4;
    --teal: #45b3ae;
    --green: #7cc242;
    --text: #e9e9e9;
    --muted: #bdbdbd;
  }
  * { margin: 0; padding: 0; box-sizing: border-box; }
  html, body { width: 1200px; height: 930px; overflow: hidden; }
  body {
    background: var(--stage);
    font-family: "Montserrat", sans-serif;
    position: relative;
  }
  .card {
    position: absolute;
    width: 560px;
    height: 320px;
    background: var(--card);
    border-radius: 14px;
    border-bottom: 7px solid var(--card-edge);
    box-shadow: 0 18px 40px rgba(0,0,0,.45);
    color: var(--text);
  }
  .card--front { left: 150px; top: 120px; }
  .card--back { left: 490px; top: 480px; }

  /* front */
  .front-brand {
    position: absolute;
    left: 0; right: 0; top: 108px;
    text-align: center;
  }
  .front-brand__name {
    display: inline-flex;
    align-items: center;
    gap: 12px;
    font-size: 30px;
    font-weight: 600;
    color: var(--green);
    letter-spacing: -0.5px;
  }
  .front-brand__dot {
    width: 18px; height: 18px;
    border-radius: 50%;
    background: var(--teal);
  }
  .front-brand__tagline {
    margin-top: 8px;
    font-size: 14px;
    letter-spacing: 2px;
    color: var(--text);
  }
  .front-url {
    position: absolute;
    left: 0; right: 0; bottom: 28px;
    text-align: center;
    font-size: 12px;
    letter-spacing: 2px;
    color: var(--muted);
  }

  /* back */
  .back-brand {
    position: absolute;
    left: 40px; top: 120px;
    width: 220px;
    text-align: center;
  }
  .back-brand__mark {
    width: 46px; height: 46px;
    margin: 0 auto 14px;
    border: 3px solid var(--teal);
    border-radius: 50%;
  }
  .back-brand__name {
    font-size: 22px;
    font-weight: 700;
    color: var(--teal);
    line-height: 1.2;
  }
  .back-divider {
    position: absolute;
    left: 282px; top: 70px;
    width: 2px; height: 130px;
    background: var(--teal);
  }
  .contact {
    position: absolute;
    left: 306px; top: 66px;
  }
  .contact__name {
    font-size: 19px;
    font-weight: 600;
    color: var(--teal);
  }
  .contact__role {
    font-size: 15px;
    color: var(--text);
    margin-bottom: 12px;
  }
  .contact__list { list-style: none; }
  .contact__item {
    display: flex;
    align-items: center;
    gap: 10px;
    font-size: 12.5px;
    line-height: 22px;
    color: var(--text);
  }
  .contact__icon { width: 12px; height: 12px; flex: none; }
  .address {
    position: absolute;
    right: 34px; bottom: 26px;
    font-size: 13.5px;
    color: var(--text);
    letter-spacing: .3px;
  }
</style>
</head>
<body>

<section class="card card--front" aria-label="Card front">
  <div class="front-brand">
    <div class="front-brand__name"><span class="front-brand__dot"></span>BrightHarborTrade.example</div>
    <p class="front-brand__tagline">Activities-Dining-Health-Beauty</p>
  </div>
  <p class="front-url">www.amberledgepartners.example</p>
</section>

<section class="card card--back" aria-label="Card back">
  <div class="back-brand">
    <div class="back-brand__mark"></div>
    <div class="back-brand__name">Amber Ledge Partners</div>
  </div>
  <div class="back-divider"></div>
  <div class="contact">
    <p class="contact__name">Daniel Verhoek</p>
    <p class="contact__role">Founder</p>
    <ul class="contact__list">
      <li class="contact__item">
        <svg class="contact__icon" viewBox="0 0 12 12"><rect x="3" y="0.5" width="6" height="11" rx="1.2" fill="none" stroke="#45b3ae" stroke-width="1.2"/></svg>
        0400 555 273
      </li>
      <li class="contact__item">
        <svg class="contact__icon" viewBox="0 0 12 12"><rect x="0.5" y="2.5" width="11" height="7" fill="#45b3ae"/><path d="M0.5 2.5 L6 7 L11.5 2.5" fill="none" stroke="#1f1f20" stroke-width="1"/></svg>
        info@brightharbortrade.example
      </li>
      <li class="contact__item">
        <svg class="contact__icon" viewBox="0 0 12 12"><circle cx="5" cy="5" r="3.5" fill="none" stroke="#45b3ae" stroke-width="1.5"/><line x1="7.6" y1="7.6" x2="11" y2="11" stroke="#45b3ae" stroke-width="1.8"/></svg>
        www.brightharbortrade.example
      </li>
    </ul>
  </div>
  <p class="address">4870 West 63rd Avenue, Suite C207 Phoenix AZ 85731</p>
</section>

</body>
</html>
```